Cleaning Service Company In need of Good Web presence.

The company is a cleaning service company which provides professional staff and service for cleaning. This is a project to build a site that is both solid and a strong recognition of our organization. It is supposed to show quality, cleanliness, professionalism. The use of images and art for imagery is all good just to have a site that is consistent and solid. There might be a chance to make stationary, logo and business cars if someone feels they can build a brand that is consistent. The image we are going for is clean solid and to stand out. Finally stationary should not be expensive to print.

Current logo is attached and can be used or can be made more creative.

Target Market(s)

Corporate and Government entities, that will feel that this company has a brand that sets it apart from the rest. The company is new so the modification of the logo will not be an issue if a more solid brand come out of this project. The idea is to have a clean consistent product that stands our from others in terms of website, stationary, etc

Industry/Entity Type

Cleaning Service

Contact Information for Business Card

P.O.Box 51947
Riffa
Kingdom of Bahrain

Logo Text

Harbor Lane Services

Number of Pages Required

4 page

Font styles to use
Sans Serif

Colors
abd036
cadf82
eaf2ce
9bcb3b

Requirements
Must have
• Green Color to be used in order to stick to the name. Also the creativity and boldness in an elegant manner.
Nice to have
• Arabic name of company
• هاربر لين سرفسس ذ.م.م
• if cannot be put at least make a location should be chosen
• Also could be a bit of 3D given to the logo if it could stay elegent.
Should not have
• Should not show people cleaning.

```html
<!DOCTYPE html>
<html lang="en">
<head>
<meta charset="utf-8">
<title>Harbor Lane Services</title>
<link href="https://fonts.googleapis.com/css2?family=Jost:wght@300;400;500;600&family=Noto+Kufi+Arabic:wght@500&display=swap" rel="stylesheet">
<style>
:root{
  --green:#9bcb3b;
  --green-mid:#abd036;
  --green-soft:#cadf82;
  --green-pale:#eaf2ce;
  --forest:#1d7a3a;
  --forest-deep:#15602c;
  --ink:#2f3a2a;
  --grey:#6f6f6f;
  --line:#e3e3e3;
  --white:#ffffff;
}
*{box-sizing:border-box;margin:0;padding:0}
html,body{width:1200px;height:2840px;overflow:hidden}
body{font-family:"Jost",Arial,sans-serif;color:var(--ink);background:var(--white);position:relative}
.abs{position:absolute}

/* header */
.hero{left:0;top:0;width:1200px;height:680px;background:linear-gradient(90deg,#f1f3f2 0%,#e6ebe9 45%,#d9dedc 70%,#c9cfcc 100%)}
.brand{left:120px;top:20px;display:flex;align-items:center;gap:14px}
.brand-mark{width:150px;height:150px;border-radius:50%;background:var(--green);border:6px solid var(--white);box-shadow:0 0 0 3px var(--green);display:flex;align-items:center;justify-content:center;text-align:center;padding:18px}
.brand-name{color:var(--white);font-weight:600;font-size:19px;line-height:1.15;text-transform:uppercase}
.phone-top{right:130px;top:18px;font-size:22px;font-weight:500;color:var(--ink);display:flex;align-items:center;gap:10px}
.nav{left:420px;top:56px;display:flex;gap:38px;font-size:17px;font-weight:500;text-transform:uppercase;color:var(--green)}
.nav a{text-decoration:none;color:inherit;padding:6px 12px}
.nav a.active{background:var(--green);color:var(--white);border-radius:18px}
.hero-title{left:120px;top:290px;font-size:44px;font-weight:400;line-height:1.15;color:var(--ink)}
.hero-title span{color:var(--forest)}
.hero-dots{left:120px;top:460px;display:flex;gap:10px}
.hero-dots i{width:14px;height:14px;border-radius:50%;background:#b8bcba}
.hero-dots i:first-child{background:var(--white);border:2px solid #a0a4a2}

/* services */
.services{left:0;top:560px;width:1200px;height:390px;background:var(--white)}
.services-band{left:0;top:560px;width:1200px;height:180px;background:var(--white)}
.service{width:300px;height:300px;border-radius:50%;background:var(--green);border:8px solid var(--white);box-shadow:0 0 0 4px var(--green);top:600px;display:flex;flex-direction:column;align-items:center;justify-content:center;text-align:center;color:var(--white);padding:30px}
.service.light{background:var(--green-soft);box-shadow:0 0 0 4px var(--green-soft);color:var(--forest-deep)}
.service h3{font-size:25px;font-weight:500;margin:12px 0 6px}
.service p{font-size:14px;line-height:1.35;max-width:210px}

/* welcome */
.welcome-photo{left:0;top:952px;width:560px;height:480px;background:linear-gradient(135deg,#e9e4dc 0%,#d8d2c8 55%,#bfb7ab 100%)}
.welcome-body{left:560px;top:952px;width:640px;height:480px;background:linear-gradient(90deg,#f4f5f4,#e9ecea)}
.welcome-title{left:640px;top:1040px;font-size:40px;font-weight:400;color:var(--forest)}
.welcome-arabic{left:640px;top:1088px;font-family:"Noto Kufi Arabic",Arial,sans-serif;font-size:32px;font-weight:500;color:var(--ink);direction:rtl}
.welcome-text{left:640px;top:1160px;width:460px;font-size:15px;line-height:1.55;color:var(--grey)}
.btn{left:640px;top:1280px;border:2px solid var(--forest);color:var(--forest);font-size:15px;padding:8px 20px;font-weight:500}

/* testimonials */
.testimonials{left:0;top:1432px;width:1200px;height:408px;background:var(--green)}
.section-title{width:1200px;text-align:center;font-size:36px;font-weight:400}
.testimonials .section-title{position:absolute;top:40px;color:var(--white)}
.title-rule{width:120px;height:2px;left:540px}
.quote-avatar{left:280px;top:1582px;width:160px;height:160px;border-radius:50%;border:6px solid var(--white);background:linear-gradient(160deg,#3b3b3d,#6b6662)}
.quote{left:480px;top:1580px;width:480px;color:var(--white);font-size:17px;line-height:1.5}
.quote-mark{font-size:56px;line-height:0.6;font-weight:600}
.quote-author{margin-top:10px;font-style:normal;font-size:15px}
.arrow{top:1620px}

/* projects */
.projects-title{top:1885px;color:var(--green)}
.project{top:1952px;width:232px;height:336px}
.project .label{position:absolute;left:0;bottom:0;width:100%;height:36px;background:rgba(40,40,40,.72);color:var(--white);font-size:16px;text-align:center;line-height:36px}
.skyline{left:0;top:2296px;width:1200px;height:144px;background:linear-gradient(180deg,#ffffff 0%,#eef0ee 60%,#e2e5e2 100%)}

/* footer */
.footer{left:0;top:2440px;width:1200px;height:320px;background:var(--forest)}
.col{top:2510px;color:var(--white)}
.col h4{font-size:26px;font-weight:400;margin-bottom:10px}
.col li{list-style:none;font-size:16px;line-height:1.55}
.contact-row{display:flex;align-items:center;gap:10px;font-size:16px;line-height:1.6}
.social{display:flex;gap:12px;margin-top:4px}
.social i{width:30px;height:30px;border-radius:50%;background:var(--green)}
.bottom-bar{left:0;top:2760px;width:1200px;height:80px;background:var(--forest-deep);color:#cfe2cf;font-size:14px;text-align:center;line-height:80px}
</style>
</head>
<body>

<header>
  <div class="abs hero" role="img" aria-label="Bright office interior with a staff member in a headscarf holding a duster"></div>
  <div class="abs brand">
    <div class="brand-mark"><span class="brand-name">Harbor Lane Services</span></div>
  </div>
  <div class="abs phone-top">
    <svg width="22" height="22" viewBox="0 0 24 24" aria-hidden="true"><path fill="#2f3a2a" d="M6.6 10.8a15.1 15.1 0 0 0 6.6 6.6l2.2-2.2a1 1 0 0 1 1-.25 11.4 11.4 0 0 0 3.6.57 1 1 0 0 1 1 1V20a1 1 0 0 1-1 1A17 17 0 0 1 3 4a1 1 0 0 1 1-1h3.5a1 1 0 0 1 1 1c0 1.25.2 2.45.57 3.57a1 1 0 0 1-.25 1z"/></svg>
    (973) 1740 5512
  </div>
  <nav class="abs nav">
    <a class="active">Home</a><a>About us</a><a>Services</a><a>Blogs</a><a>Gallery</a><a>Contact</a>
  </nav>
  <h1 class="abs hero-title">Govt Agencies &amp;<br><span>Office Cleaning Services</span></h1>
  <div class="abs hero-dots"><i></i><i></i><i></i><i></i></div>
</header>

<section>
  <div class="abs services-band"></div>
  <div class="abs service" style="left:130px">
    <svg width="60" height="60" viewBox="0 0 60 60" aria-hidden="true"><rect x="14" y="22" width="32" height="30" rx="3" fill="none" stroke="#fff" stroke-width="3"/><path d="M20 22a10 10 0 0 1 20 0" fill="none" stroke="#fff" stroke-width="3"/></svg>
    <h3>Office Cleaning</h3>
    <p>Daily desk, floor and kitchen care for busy offices.</p>
  </div>
  <div class="abs service" style="left:450px">
    <svg width="60" height="60" viewBox="0 0 60 60" aria-hidden="true"><rect x="12" y="10" width="36" height="40" fill="none" stroke="#fff" stroke-width="3"/><path d="M30 10v40M12 30h36" stroke="#fff" stroke-width="3"/></svg>
    <h3>Window Cleaning</h3>
    <p>Streak free glass inside and out, any height.</p>
  </div>
  <div class="abs service light" style="left:778px">
    <svg width="60" height="60" viewBox="0 0 60 60" aria-hidden="true"><rect x="10" y="16" width="40" height="28" rx="4" fill="none" stroke="#15602c" stroke-width="3"/><path d="M10 30h40" stroke="#15602c" stroke-width="3"/></svg>
    <h3>Carpet &amp; Floor</h3>
    <p>Deep vacuum, wash and polish for every floor.</p>
  </div>
</section>

<section>
  <div class="abs welcome-photo" role="img" aria-label="Smiling team member in a headscarf standing in a bright office"></div>
  <div class="abs welcome-body"></div>
  <h2 class="abs welcome-title">Welcome to</h2>
  <p class="abs welcome-arabic" lang="ar">هاربر لين سرفسس ذ.م.م</p>
  <p class="abs welcome-text">Our trained teams keep public offices and corporate spaces spotless every day. We work around your schedule, use safe products, and check each site against a clear quality list so your staff and visitors walk into a clean, calm space.</p>
  <div class="abs btn">Learn More</div>
</section>

<section>
  <div class="abs testimonials"><h2 class="section-title">Client Testimonials</h2></div>
  <div class="abs title-rule" style="top:1530px;background:var(--white)"></div>
  <div class="abs quote-avatar" role="img" aria-label="Client portrait"></div>
  <blockquote class="abs quote">
    <span class="quote-mark">“</span> Their crew arrived on time, worked quietly and left our ministry offices brighter than ever. We have trusted them for a full year now. <span class="quote-mark">”</span>
    <cite class="quote-author" style="display:block">By Author Name</cite>
  </blockquote>
  <svg class="abs arrow" style="left:160px" width="24" height="40" viewBox="0 0 24 40" aria-hidden="true"><path d="M20 4 4 20l16 16" fill="none" stroke="#fff" stroke-width="3"/></svg>
  <svg class="abs arrow" style="left:1010px" width="24" height="40" viewBox="0 0 24 40" aria-hidden="true"><path d="M4 4l16 16L4 36" fill="none" stroke="#fff" stroke-width="3"/></svg>
</section>

<section>
  <h2 class="abs section-title projects-title">Cleanig Projects</h2>
  <div class="abs title-rule" style="top:1935px;background:var(--green)"></div>
  <div class="abs project" style="left:112px;background:linear-gradient(160deg,#e9eceb,#b9bfbd)" role="img" aria-label="Clean white office with desks"><span class="label">Project Title here</span></div>
  <div class="abs project" style="left:355px;background:linear-gradient(160deg,#bcd6ea,#5c7f9c)" role="img" aria-label="Glass office corridor"><span class="label">Project Title here</span></div>
  <div class="abs project" style="left:598px;background:linear-gradient(160deg,#dfe3e6,#8f9aa2)" role="img" aria-label="Meeting room with large windows"><span class="label">Project Title here</span></div>
  <div class="abs project" style="left:841px;background:linear-gradient(160deg,#e6e2da,#9a938a)" role="img" aria-label="Workstation with computer screens"><span class="label">Project Title here</span></div>
  <div class="abs skyline" role="img" aria-label="Faint city skyline silhouette"></div>
</section>

<footer>
  <div class="abs footer"></div>
  <div class="abs col" style="left:112px"><h4>Quick Links</h4><ul><li>Home</li><li>About us</li><li>Our Services</li><li>Why Us</li></ul></div>
  <div class="abs col" style="left:290px"><h4>Resources</h4><ul><li>Prices</li><li>Testimonials</li><li>Contact Us</li></ul></div>
  <div class="abs col" style="left:480px;width:320px">
    <h4>Contact Us</h4>
    <p style="font-size:15px;line-height:1.5">Building 214, Road 37, Riffa<br>Kingdom of Bahrain</p>
    <div class="contact-row"><svg width="16" height="16" viewBox="0 0 24 24" aria-hidden="true"><path fill="#fff" d="M6.6 10.8a15.1 15.1 0 0 0 6.6 6.6l2.2-2.2a1 1 0 0 1 1-.25 11.4 11.4 0 0 0 3.6.57 1 1 0 0 1 1 1V20a1 1 0 0 1-1 1A17 17 0 0 1 3 4a1 1 0 0 1 1-1h3.5a1 1 0 0 1 1 1c0 1.25.2 2.45.57 3.57a1 1 0 0 1-.25 1z"/></svg>(973) 1762 3308</div>
    <div class="contact-row"><svg width="16" height="16" viewBox="0 0 24 24" aria-hidden="true"><rect x="2" y="5" width="20" height="14" fill="none" stroke="#fff" stroke-width="2"/><path d="M2 6l10 7 10-7" fill="none" stroke="#fff" stroke-width="2"/></svg>hello@harborlane.example</div>
  </div>
  <div class="abs col" style="left:840px"><h4>Follow Us</h4><div class="social"><i></i><i></i><i></i><i></i><i></i></div></div>
  <div class="abs bottom-bar">© 2016 Harbor Lane Services. All rights reserved. Terms of Use</div>
</footer>

</body>
</html>
```